Redesign of business card for Cedar Ridge Mechanical

We are looking for a new design for our business cards for Cedar Ridge Mechanical. We are a plumbing & HVAC construction company, operating on the West Coast of Canada and USA. Logo attached.
Industry/Entity Type
Construction - Plumbing & HVAC
Contact Information for Business Card
Name, address, phone numbers, email, website address
Look and feel
Each slider illustrates characteristics of the customer's brand and the style your logo design should communicate.

```html
<!DOCTYPE html>
<html lang="en">
<head>
<meta charset="utf-8">
<title>Cedar Ridge Mechanical — Business Card</title>
<link href="https://fonts.googleapis.com/css2?family=Oswald:wght@500&family=Montserrat:wght@400;700&display=swap" rel="stylesheet">
<style>
  :root {
    --backdrop: #8a6c4c;
    --card-front: #ffffff;
    --card-back: #161616;
    --ink: #1c1c1c;
    --ink-soft: #2a2a2a;
    --mark-on-dark: #3a3a3a;
  }
  * { margin: 0; padding: 0; box-sizing: border-box; }
  html, body { width: 900px; height: 1200px; overflow: hidden; }
  body {
    background: var(--backdrop);
    position: relative;
    font-family: "Montserrat", Arial, sans-serif;
    color: var(--ink);
  }
  .card {
    position: absolute;
    left: 80px;
    width: 742px;
    height: 440px;
    border-radius: 22px;
    box-shadow: 0 6px 14px rgba(0,0,0,0.35);
  }
  .card-front { top: 131px; background: var(--card-front); }
  .card-back { top: 638px; background: var(--card-back); }

  .company-heading {
    position: absolute;
    left: 24px; top: 54px;
    font-family: "Oswald", "Arial Narrow", sans-serif;
    font-weight: 500;
    font-size: 37px;
    letter-spacing: 1.5px;
    line-height: 1;
    text-transform: uppercase;
    color: var(--ink);
  }
  .person { position: absolute; left: 34px; top: 150px; }
  .person-name { font-weight: 700; font-size: 25px; line-height: 1.1; }
  .person-role { font-size: 15.5px; margin-top: 4px; }

  .address {
    position: absolute; left: 34px; top: 234px;
    font-size: 16px; line-height: 21px;
  }
  .contact-list {
    position: absolute; left: 36px; top: 316px;
    list-style: none;
    font-size: 15.5px;
  }
  .contact-list li {
    display: flex; align-items: center; gap: 10px;
    height: 30px;
  }
  .contact-list svg { width: 16px; height: 16px; fill: var(--ink); flex: none; }

  .brand-mark {
    position: absolute;
    display: flex; align-items: center;
    font-family: "Oswald", "Arial Narrow", sans-serif;
    font-weight: 500;
    text-transform: uppercase;
    line-height: 1;
  }
  .brand-mark-front {
    left: 322px; top: 140px; width: 364px; height: 230px;
    gap: 18px; color: var(--ink);
    font-size: 48px;
  }
  .brand-mark-front .brand-square {
    width: 40px; height: 40px; background: var(--ink); flex: none;
  }
  .brand-mark-back {
    left: 0; right: 0; top: 0; bottom: 0;
    justify-content: center; gap: 22px;
    color: var(--mark-on-dark);
    font-size: 52px;
    letter-spacing: 1px;
  }
  .brand-mark-back .brand-square {
    width: 44px; height: 44px; background: var(--mark-on-dark); flex: none;
  }
</style>
</head>
<body>

  <section class="card card-front" aria-label="Business card front">
    <h1 class="company-heading">Cedar Ridge Mechanical</h1>

    <div class="person">
      <p class="person-name">Daniel Reyes</p>
      <p class="person-role">Managing Director</p>
    </div>

    <address class="address" style="font-style:normal">
      57 Birch Hollow Lane<br>
      Sumner, WA 98390
    </address>

    <ul class="contact-list">
      <li>
        <svg viewBox="0 0 24 24" aria-hidden="true"><path d="M6.6 10.8a15.2 15.2 0 0 0 6.6 6.6l2.2-2.2a1 1 0 0 1 1-.25 11.4 11.4 0 0 0 3.6.57 1 1 0 0 1 1 1V20a1 1 0 0 1-1 1A17 17 0 0 1 3 4a1 1 0 0 1 1-1h3.5a1 1 0 0 1 1 1c0 1.25.2 2.45.57 3.57a1 1 0 0 1-.25 1z"/></svg>
        <span>555.214.7730</span>
      </li>
      <li>
        <svg viewBox="0 0 24 24" aria-hidden="true"><path d="M2 5h20v2l-10 6L2 7z M2 9l10 6 10-6v10H2z"/></svg>
        <span>info@cedarridgemechanical.com</span>
      </li>
      <li>
        <svg viewBox="0 0 24 24" aria-hidden="true"><path d="M12 2a10 10 0 1 0 0 20 10 10 0 0 0 0-20zm6.9 6h-3a15 15 0 0 0-1.3-3.9A8 8 0 0 1 18.9 8zM12 4c.8 1.1 1.5 2.5 1.9 4h-3.8c.4-1.5 1.1-2.9 1.9-4zM4.3 14a8 8 0 0 1 0-4h3.4a16 16 0 0 0 0 4zm.8 2h3a15 15 0 0 0 1.3 3.9A8 8 0 0 1 5.1 16zm3-8h-3a8 8 0 0 1 4.3-3.9A15 15 0 0 0 8.1 8zM12 20c-.8-1.1-1.5-2.5-1.9-4h3.8c-.4 1.5-1.1 2.9-1.9 4zm2.3-6H9.7a14 14 0 0 1 0-4h4.6a14 14 0 0 1 0 4zm.3 5.9a15 15 0 0 0 1.3-3.9h3a8 8 0 0 1-4.3 3.9zm1.7-5.9a16 16 0 0 0 0-4h3.4a8 8 0 0 1 0 4z"/></svg>
        <span>www.cedarridgemechanical.com</span>
      </li>
    </ul>

    <div class="brand-mark brand-mark-front">
      <span class="brand-square" aria-hidden="true"></span>
      <span class="brand-name">Cedar Ridge<br>Mechanical</span>
    </div>
  </section>

  <section class="card card-back" aria-label="Business card back">
    <div class="brand-mark brand-mark-back">
      <span class="brand-square" aria-hidden="true"></span>
      <span class="brand-name">Cedar Ridge Mechanical</span>
    </div>
  </section>

</body>
</html>
```